Roadside building business signage for a holistic health clinic.

Replace signs as shown in the attached file. They are perforated stickers that go on the windows as shown. Looking for something that has our logo and says the name of the practice with logo (Fernridge Health & Wellness) also boldly says Acupuncture, IV Vitamins, and Holistic Health.
Possibly our phone number as well 318-562-7041
Updates

Please don't use pink except the logo. Earthy, organic tone colors appreciated.

Need of eye catching window signage of a holistic clinic on a brick building. Pink, purple, sage green, white color. Logo is pink on a white background. Please don't overload with too much pink. Words to include are "Fernridge Health and Wellness(name of business)", "Direct Primary Care", " Medical acupuncture", "IV Vitamin Therapy", "fernridgecareclinic.example","318-562-7041".

Target Market(s)

People will see in their cars passing by the building. Busy roadside so need to be visible while passing in fast speed.

Industry/Entity Type

Health & Wellness

Font styles to use
Sans Serif

Colors

Designer to choose colors to be used in the design.

Requirements
Must have
• On sign must have words Holistic Medicine, Medical Acupuncture, Direct Primary Care and IV vitamins.
Nice to have
• Simple, minimalistic, artistic yet has clear message. White, Black, Violet, Pink (logo), Dark green, Sage green.
Should not have
• Bold colors (red, yellow, blue), same tone colors. Blue waves on the current signage (uploaded file) must go.

```html
<!DOCTYPE html>
<html lang="en">
<head>
<meta charset="utf-8">
<title>Fernridge Health &amp; Wellness – Window Signage</title>
<link rel="stylesheet" href="https://fonts.googleapis.com/css2?family=Marcellus&display=swap">
<style>
  :root {
    --wall: #5f5f5f;
    --cream: #f6efe2;
    --cream-light: #fdfcf8;
    --forest: #0d4a3a;
    --sage: #618c76;
    --sage-soft: #aac4b8;
    --sage-pale: #d2ded7;
    --text-light: #f4f1e8;
    --bloom: #d9448a;
  }
  * { box-sizing: border-box; margin: 0; padding: 0; }
  html, body { width: 1200px; height: 792px; overflow: hidden; background: var(--wall); }
  body { position: relative; font-family: "Marcellus", sans-serif; }

  .pane { position: absolute; overflow: hidden; }

  /* arch transom */
  .arch { top: 77px; width: 200px; height: 214px; background: var(--cream); }
  .arch--left { left: 478px; border-top-left-radius: 100% 100%; }
  .arch--right { left: 697px; border-top-right-radius: 100% 100%; }
  .arch__headline {
    position: absolute; top: 78px;
    font-size: 29px; line-height: 29px; color: var(--forest);
    letter-spacing: 0.5px;
  }
  .arch--left .arch__headline { right: 18px; text-align: right; }
  .arch--right .arch__headline { left: 18px; text-align: left; }

  /* middle band */
  .brand-pane {
    top: 297px; height: 219px; width: 200px;
    background: linear-gradient(to bottom, var(--cream), var(--cream-light) 70%);
  }
  .brand-pane__waves {
    position: absolute; left: 0; right: 0; bottom: 0; height: 80px;
    background: linear-gradient(to bottom, rgba(170,196,184,0) 0%, var(--sage-pale) 45%, var(--sage-soft) 100%);
  }
  .brand {
    position: absolute; left: 0; right: 0; top: 36px;
    display: flex; flex-direction: column; align-items: center;
    color: var(--forest);
  }
  .brand__dot { width: 46px; height: 46px; border-radius: 50%; background: var(--bloom); margin-bottom: 18px; }
  .brand__name { font-size: 25px; letter-spacing: 3px; line-height: 26px; }
  .brand__tagline { font-size: 8px; letter-spacing: 3.2px; margin-top: 4px; }

  /* lower band */
  .info-pane { top: 522px; height: 219px; background: var(--sage); color: var(--text-light); }
  .services {
    position: absolute; top: 55px; list-style: none;
    font-size: 16.5px; line-height: 32px;
  }
  .info-pane--services-left .services { right: 18px; text-align: right; }
  .info-pane--services-right .services { left: 18px; text-align: left; }

  .contact { position: absolute; left: 0; right: 0; top: 88px; text-align: center; }
  .contact__phone {
    display: inline-block; width: 127px; height: 26px; line-height: 24px;
    border: 1px solid var(--forest); border-radius: 5px;
    font-size: 17px; letter-spacing: 0.3px;
  }
  .contact__web { display: block; margin-top: 5px; font-size: 10px; letter-spacing: 0.3px; }

  .leaf-art { position: absolute; bottom: 0; height: 70px; background: var(--cream); opacity: 0.9; }
</style>
</head>
<body>
  <!-- arch transom -->
  <div class="pane arch arch--left">
    <p class="arch__headline">DIRECT<br>HOLISTIC<br>PRIMARY<br>CARE</p>
  </div>
  <div class="pane arch arch--right">
    <p class="arch__headline">DIRECT<br>HOLISTIC<br>PRIMARY<br>CARE</p>
  </div>

  <!-- middle band -->
  <div class="pane brand-pane" style="left:271px;">
    <div class="brand-pane__waves" role="img" aria-label="Soft sage wave shapes"></div>
  </div>
  <div class="pane brand-pane" style="left:477px;">
    <div class="brand-pane__waves" role="img" aria-label="Soft sage wave shapes"></div>
    <div class="brand">
      <span class="brand__dot"></span>
      <span class="brand__name">FERNRIDGE</span>
      <span class="brand__tagline">HEALTH &amp; WELLNESS</span>
    </div>
  </div>
  <div class="pane brand-pane" style="left:697px; width:201px;">
    <div class="brand-pane__waves" role="img" aria-label="Soft sage wave shapes"></div>
    <div class="brand">
      <span class="brand__dot"></span>
      <span class="brand__name">FERNRIDGE</span>
      <span class="brand__tagline">HEALTH &amp; WELLNESS</span>
    </div>
  </div>
  <div class="pane brand-pane" style="left:904px; width:199px;">
    <div class="brand-pane__waves" role="img" aria-label="Soft sage wave shapes"></div>
  </div>

  <!-- lower band -->
  <div class="pane info-pane" style="left:65px; width:200px;">
    <div class="leaf-art" style="left:128px; width:100px; border-radius:50px 0 0 0;" role="img" aria-label="Line-drawn ginkgo leaf decoration"></div>
  </div>
  <div class="pane info-pane" style="left:271px; width:200px;">
    <div class="contact">
      <span class="contact__phone">318-562-7041</span>
      <span class="contact__web">www.fernridgecareclinic.example</span>
    </div>
    <div class="leaf-art" style="left:0; width:72px; border-radius:0 50px 0 0;" role="img" aria-label="Line-drawn ginkgo leaf decoration"></div>
  </div>
  <div class="pane info-pane info-pane--services-left" style="left:477px; width:200px;">
    <ul class="services">
      <li>Holistic Medicine</li>
      <li>Medical Acupuncture</li>
      <li>Direct Primary Care</li>
      <li>IV vitamins</li>
    </ul>
  </div>
  <div class="pane info-pane info-pane--services-right" style="left:697px; width:200px;">
    <ul class="services">
      <li>Holistic Medicine</li>
      <li>Medical Acupuncture</li>
      <li>Direct Primary Care</li>
      <li>IV vitamins</li>
    </ul>
  </div>
  <div class="pane info-pane" style="left:903px; width:200px;">
    <div class="contact">
      <span class="contact__phone">318-562-7041</span>
      <span class="contact__web">www.fernridgecareclinic.example</span>
    </div>
    <div class="leaf-art" style="left:127px; width:73px; border-radius:50px 0 0 0;" role="img" aria-label="Line-drawn ginkgo leaf decoration"></div>
  </div>
</body>
</html>
```